pet resort day care for our buisiness

we need a new web design for our pet center in Florida , we are provide the following services -
1. dog day car
2.dog/cat boarding
3. dog grooming
4. Dog training
5.pet food toy and clothing
our current websit is -http://www.tindlewoodpetcenter.com/
we are looking for a fresh new design that will reflect the change that we have made in the vusness from renovationnto the facelaty new management and new servises
Target Market(s)
Dog Lover , Upmarket
Industry/Entity Type
Pet
Number of Pages Required
5+ page
Font styles to use
Sans Serif
Requirements
Must have
- clean design , easy to understand and navigate , our target is the upmarket costumer how are dog lover
Should not have
- NOOO of the shelf design , confusing design , brown colors

```html
<!DOCTYPE html>
<html lang="en">
<head>
<meta charset="utf-8">
<title>Tindlewood Pet Center</title>
<link rel="stylesheet" href="https://fonts.googleapis.com/css2?family=Delius&family=Open+Sans:wght@400;600;700&display=swap">
<style>
:root{
  --pink:#ec4567;
  --pink-deep:#de3458;
  --footer:#ef4a6a;
  --footer-bar:#e23c5d;
  --ink:#3d3d45;
  --muted:#5b5b63;
  --line:#e6e6e6;
  --gold:#d4a932;
  --sun:#f7d43a;
  --white:#ffffff;
}
*{box-sizing:border-box;margin:0;padding:0}
html,body{width:1200px;height:2338px;overflow:hidden}
body{position:relative;background:var(--white);font-family:"Delius",sans-serif;color:var(--ink)}
.abs{position:absolute}

/* header */
.top-rule{left:0;top:0;width:1200px;height:4px;background:var(--pink)}
.brand{left:97px;top:14px;display:flex;align-items:center;gap:10px}
.brand-mark{width:22px;height:22px;border-radius:50%;background:var(--pink)}
.brand-name{font-family:"Delius",sans-serif;font-size:30px;color:var(--pink);line-height:1.1;width:170px}
.connected{left:628px;top:18px;display:flex;align-items:center;gap:10px;font-family:"Open Sans",sans-serif;font-size:11px;font-weight:700;color:#7b7b7b;letter-spacing:.3px}
.connected .dot{width:17px;height:17px;border-radius:3px;display:inline-block}
.phone-tab{left:868px;top:0;width:232px;height:50px;background:var(--pink);border-radius:0 0 22px 22px;display:flex;align-items:center;justify-content:center;gap:8px;color:var(--white);font-family:"Open Sans",sans-serif}
.phone-tab small{font-size:11px;font-weight:700}
.phone-tab strong{font-size:17px;font-weight:600}
.nav{left:397px;top:90px;display:flex;gap:26px;font-family:"Open Sans",sans-serif;font-size:11.5px;font-weight:700;color:#333}
.nav .active{color:var(--pink)}

/* hero */
.hero{left:0;top:145px;width:1200px;height:541px;background:linear-gradient(180deg,#8a7a3a 0%,#6d5a2e 35%,#55732f 72%,#5f8a35 100%)}
.hero-title{left:97px;top:318px;font-family:"Open Sans",sans-serif;font-weight:600;font-size:30px;line-height:46px;text-transform:uppercase}
.hero-title .a{color:var(--pink)}
.hero-title .b{color:var(--white)}
.arrow{top:335px;width:52px;height:52px;border-radius:50%;background:rgba(255,255,255,.35);display:flex;align-items:center;justify-content:center}

/* welcome */
.welcome{left:97px;top:712px;width:660px}
.welcome h1{font-size:25px;color:var(--pink);font-weight:400;margin-bottom:18px}
.welcome .lead{font-size:13.5px;line-height:24px;color:var(--ink);margin-bottom:12px}
.welcome .body{font-size:11.5px;line-height:23px;color:var(--ink)}
.btn{display:inline-block;background:var(--pink);color:var(--white);font-family:"Delius",sans-serif;border-radius:2px}
.welcome .btn{margin-top:24px;font-size:14px;padding:10px 15px}
.video{left:790px;top:722px;width:308px;height:226px;border:4px solid var(--white);box-shadow:0 0 0 1px #ddd;background:linear-gradient(160deg,#cdbfae,#8f8a72 60%,#6f6a52)}
.play{left:932px;top:820px;width:32px;height:24px;background:#e62b2b;border-radius:6px}
.divider{left:0;top:998px;width:1200px;height:1px;background:var(--line)}

/* services */
.services-title{left:97px;top:1020px;font-family:"Open Sans",sans-serif;font-size:23px;font-weight:600;color:#666}
.pager{left:1052px;top:1021px;width:48px;height:48px;border-radius:50%;border:1px solid var(--line);display:flex;align-items:center;justify-content:center;color:var(--pink);font-size:16px}
.card{top:1083px;width:243px;height:357px;border:1px solid var(--line);background:var(--white);padding:3px}
.card .photo{height:168px}
.card h3{font-size:18px;font-weight:400;color:var(--pink);margin:14px 0 0 17px}
.card p{font-size:11px;line-height:19px;color:var(--muted);margin:10px 17px 0}
.card .btn{margin:22px 0 0 17px;font-size:13px;padding:8px 16px}

/* band */
.band{left:0;top:1476px;width:1200px;height:546px;background:linear-gradient(110deg,#e7e3df 0%,#c9c0b5 40%,#d7cbbf 65%,#b98f5a 85%,#d9c7a8 100%)}
.band-text{left:97px;top:1655px}
.band-text h2{font-family:"Open Sans",sans-serif;font-weight:600;font-size:25px;line-height:42px;color:var(--pink)}
.band-text .hours-a{font-size:14.5px;color:var(--sun);margin-top:18px}
.band-text .hours-b{font-size:14.5px;color:var(--white);margin-top:16px}

/* footer */
.footer{left:0;top:2022px;width:1200px;height:246px;background:var(--footer)}
.fcol{top:2054px;color:var(--white);font-family:"Open Sans",sans-serif}
.fcol h4{font-size:12px;font-weight:700;text-transform:uppercase;display:flex;align-items:center;gap:8px;margin-bottom:14px}
.fcol ul{list-style:none;font-size:11px;font-weight:600}
.fcol li{line-height:28px}
.fsep{top:2050px;width:1px;height:190px;background:rgba(255,255,255,.22)}
.email-field{width:234px;height:36px;background:var(--white);font-size:10px;color:#555;padding:11px 10px;margin-top:12px}
.submit{width:122px;height:40px;background:var(--gold);margin-top:18px;font-size:13px;font-weight:700;display:flex;align-items:center;justify-content:center}
.socials{display:flex;gap:9px;margin-top:6px}
.socials span{width:34px;height:34px;border-radius:50%;border:2px solid var(--white)}
.contact li{display:flex;gap:12px;line-height:28px}
.bottom-bar{left:0;top:2268px;width:1200px;height:70px;background:var(--footer-bar);color:var(--white);font-family:"Open Sans",sans-serif;font-size:11px;font-weight:700;display:flex;align-items:center;justify-content:center}
</style>
</head>
<body>

<div class="abs top-rule"></div>

<header>
  <div class="abs brand">
    <span class="brand-mark"></span>
    <span class="brand-name">Tindlewood</span>
  </div>
  <div class="abs connected">CONNECTED US:
    <span class="dot" style="background:#3b5998"></span>
    <span class="dot" style="background:#1da1f2"></span>
    <span class="dot" style="background:#34a853"></span>
    <span class="dot" style="background:#e52d27"></span>
  </div>
  <div class="abs phone-tab"><small>PET CENTER :</small><strong>954-555-0148</strong></div>
  <nav class="abs nav">
    <span class="active">HOME</span><span>BOARDING</span><span>DAYCARE</span><span>GROOMING</span><span>TRAINING</span><span>BOUTIQUE</span><span>BLOG</span><span>CONTACT</span><span>ABOUT US</span>
  </nav>
</header>

<section>
  <div class="abs hero" role="img" aria-label="Two dogs sitting on grass in an autumn park"></div>
  <div class="abs arrow" style="left:26px"><svg width="18" height="22" viewBox="0 0 18 22"><path d="M14 2 4 11l10 9" fill="none" stroke="#555" stroke-width="4"/></svg></div>
  <div class="abs arrow" style="left:1117px"><svg width="18" height="22" viewBox="0 0 18 22"><path d="M4 2l10 9-10 9" fill="none" stroke="#555" stroke-width="4"/></svg></div>
  <h2 class="abs hero-title"><span class="a">Tindlewood Pet</span><br><span class="b">Center in Florida</span></h2>
</section>

<section class="abs welcome">
  <h1>Welcome to Tindlewood Pet Center!</h1>
  <p class="lead">A pet paradise providing the best pet care in the greater Fort Lauderdale FL area.<br>Professional cat &amp; dog boarding, doggy daycare, pet grooming, training, holistic foods &amp; pet boutique.</p>
  <p class="body">Discover how much Tindlewood has to offer for your pet boarding needs by viewing a virtual tour of our 16,000 s/f 'Home Away From Home'. See 9,000 s/f of air conditioned space and a 4,000 s/f outdoor playground with a splash pool. Why not just come by and take a tour of our Fort Lauderdale FL retail store, grooming salon and air conditioned suites? If you prefer to set a time that is best for you.</p>
  <span class="btn">Book An Appointment Today!</span>
</section>
<div class="abs video" role="img" aria-label="Video still of a couple with their pug in a park"></div>
<div class="abs play"><svg width="32" height="24" viewBox="0 0 32 24"><path d="M13 7l8 5-8 5z" fill="#fff"/></svg></div>
<div class="abs divider"></div>

<section>
  <h2 class="abs services-title">Our Services</h2>
  <div class="abs pager">&lsaquo; &rsaquo;</div>
  <article class="abs card" style="left:98px">
    <div class="photo" role="img" aria-label="Happy dog looking out of a car window" style="background:linear-gradient(135deg,#6f8f46,#8a6a48 60%,#3b3b3b)"></div>
    <h3>Dog Day Car</h3>
    <p>Similique sunt in culpa qui officia deserunt mollitia animi, id est laborum et dolorum fuga.</p>
    <span class="btn">View More &raquo;</span>
  </article>
  <article class="abs card" style="left:352px">
    <div class="photo" role="img" aria-label="Puppy with a colourful ball" style="background:linear-gradient(135deg,#f3e3c8,#c98a4d 60%,#f08a3c)"></div>
    <h3>Dog/Cat Boarding</h3>
    <p>Similique sunt in culpa qui officia deserunt mollitia animi, id est laborum et dolorum fuga.</p>
    <span class="btn">View More &raquo;</span>
  </article>
  <article class="abs card" style="left:606px">
    <div class="photo" role="img" aria-label="Terrier being groomed with scissors" style="background:linear-gradient(135deg,#e8d5b5,#b88a4e 55%,#d9c8b0)"></div>
    <h3>Dog Grooming</h3>
    <p>Similique sunt in culpa qui officia deserunt mollitia animi, id est laborum et dolorum fuga.</p>
    <span class="btn">View More &raquo;</span>
  </article>
  <article class="abs card" style="left:860px">
    <div class="photo" role="img" aria-label="Child training a dog on a leash outdoors" style="background:linear-gradient(135deg,#7fa66a,#a8b88a 55%,#5e7a45)"></div>
    <h3>Dog Training</h3>
    <p>Similique sunt in culpa qui officia deserunt mollitia animi, id est laborum et dolorum fuga.</p>
    <span class="btn">View More &raquo;</span>
  </article>
</section>

<section>
  <div class="abs band" role="img" aria-label="Family relaxing on a sofa with a golden retriever in the foreground"></div>
  <div class="abs band-text">
    <h2>Our Fort Lauderdale FL<br>Facility is open 7 days per week</h2>
    <p class="hours-a">(Monday - Saturday 7:00 am to 7:00 pm)</p>
    <p class="hours-b">(Sunday 9:00 am to 5:00 pm)</p>
  </div>
</section>

<footer>
  <div class="abs footer"></div>
  <div class="abs fcol" style="left:97px">
    <h4><svg width="13" height="13" viewBox="0 0 13 13"><path d="M5 8l3-3M4 6 2 8a2 2 0 0 0 3 3l2-2M9 7l2-2a2 2 0 0 0-3-3L6 4" fill="none" stroke="#fff" stroke-width="1.6"/></svg>Quick Links</h4>
    <ul><li>Home</li><li>Boarding</li><li>Boutique</li><li>Blog</li><li>Contact</li><li>About Us</li></ul>
  </div>
  <div class="abs fsep" style="left:243px"></div>
  <div class="abs fcol" style="left:292px">
    <h4><svg width="14" height="11" viewBox="0 0 14 11"><rect x="0" y="0" width="14" height="11" fill="#fff"/><path d="M0 0l7 6 7-6" fill="none" stroke="#ef4a6a" stroke-width="1.4"/></svg>News Letter Signup</h4>
    <ul><li style="line-height:18px">Sign-up to be notified about news</li></ul>
    <div class="email-field">Enter Your Email</div>
    <div class="submit">SUBMIT</div>
  </div>
  <div class="abs fsep" style="left:565px"></div>
  <div class="abs fcol" style="left:600px">
    <h4><svg width="15" height="13" viewBox="0 0 15 13"><path d="M10 1h4v4M14 1 8 7M11 8v4H1V3h5" fill="none" stroke="#fff" stroke-width="1.5"/></svg>Follow Us</h4>
    <div class="socials">
      <span style="background:#3b5998"></span><span style="background:#1da1f2"></span><span style="background:#c4302b"></span><span style="background:#c0392b"></span><span style="background:#c8a22c"></span>
    </div>
  </div>
  <div class="abs fsep" style="left:835px"></div>
  <div class="abs fcol contact" style="left:860px">
    <h4><svg width="14" height="13" viewBox="0 0 14 13"><path d="M1 4c0-2 3-3 6-3s6 1 6 3v1h-3V4H4v1H1zM3 6h8l1 6H2z" fill="#fff"/></svg>Contact Us</h4>
    <ul>
      <li><svg width="9" height="28" viewBox="0 0 9 28"><path d="M4.5 9a3.5 3.5 0 0 1 3.5 3.5c0 2.5-3.5 6.5-3.5 6.5S1 15 1 12.5A3.5 3.5 0 0 1 4.5 9z" fill="#fff"/></svg>Office: 420 SE Harbor Way,</li>
      <li style="padding-left:21px">Fort Lauderdale, FL 33316</li>
      <li><svg width="9" height="28" viewBox="0 0 9 28"><rect x="2" y="9" width="5" height="10" rx="1" fill="#fff"/></svg>Mobile: 954-555-0148</li>
      <li><svg width="9" height="28" viewBox="0 0 9 28"><rect x="1" y="10" width="7" height="8" fill="#fff"/></svg>Fax: 954-555-0148</li>
      <li><svg width="9" height="28" viewBox="0 0 9 28"><rect x="0" y="11" width="9" height="7" fill="#fff"/></svg>Mail: hello@tindlewoodpet.com</li>
    </ul>
  </div>
  <div class="abs bottom-bar">TINDLEWOOD PET CENTER. &copy; 2015 &nbsp;|&nbsp; Privacy Policy</div>
</footer>

</body>
</html>
```